Business card for law firm

Need business card for new law firm. Think confident, authoritative, conservative, but not stuffy or old-fashioned.

Contact Information for Business Card

Content for card - logo (uploaded), plus the following:

Paul Whitcombe (larger font)
Managing Partner (larger font, but not as large as name)
Level 9, 7 Ferris Lane
Sydney NSW 2000
Main Tel 02 9364 2710
Direct Tel 02 8472 3159
Email paul@qvlegal.com.au
www.qvlegal.com.au

Letterhead design should include logo plus:
Level 9, 7 Ferris Lane
Sydney NSW 2000
Tel 02 8472 3159
www.qvlegal.com.au

```html
<!DOCTYPE html>
<html lang="en">
<head>
<meta charset="utf-8">
<title>Quayvale Lawyers – Business Card</title>
<link rel="stylesheet" href="https://fonts.googleapis.com/css2?family=Cinzel:wght@500&family=Roboto:wght@400&display=swap">
<style>
  :root {
    --backdrop: #202227;
    --navy: #1f2568;
    --navy-deep: #181d55;
    --paper: #ffffff;
    --ink-soft: #d9dcf0;
  }
  * { box-sizing: border-box; margin: 0; padding: 0; }
  html, body { width: 1200px; height: 900px; overflow: hidden; }
  body {
    background: var(--backdrop);
    position: relative;
    font-family: "Roboto", Arial, sans-serif;
  }
  .card {
    position: absolute;
    top: 290px;
    width: 540px;
    height: 320px;
    border-radius: 22px;
    background: linear-gradient(150deg, var(--navy) 0%, var(--navy-deep) 100%);
    overflow: hidden;
    color: var(--paper);
  }
  .card--details { left: 40px; }
  .card--brand { left: 620px; }

  .accent-band {
    position: absolute;
    top: 0;
    left: 250px;
    width: 40px;
    height: 100%;
    background: var(--paper);
  }

  .contact {
    position: absolute;
    top: 34px;
    left: 34px;
    width: 200px;
  }
  .contact__name {
    font-family: "Cinzel", Georgia, serif;
    font-weight: 500;
    font-size: 17px;
    letter-spacing: 0.5px;
    line-height: 1.1;
    text-transform: uppercase;
  }
  .contact__role {
    font-size: 11.5px;
    color: var(--ink-soft);
    margin-top: 4px;
  }
  .contact__list {
    list-style: none;
    margin-top: 30px;
    font-size: 11.5px;
    line-height: 1.65;
    color: var(--ink-soft);
  }
  .contact__list li { display: flex; align-items: center; gap: 7px; }
  .contact__list svg { width: 10px; height: 10px; flex: none; fill: var(--ink-soft); }
  .contact__address { margin-top: 8px; font-size: 11.5px; line-height: 1.65; color: var(--ink-soft); }

  .wordmark {
    position: absolute;
    display: flex;
    flex-direction: column;
    align-items: center;
    font-family: "Cinzel", Georgia, serif;
    font-weight: 500;
    color: var(--paper);
  }
  .wordmark__square {
    width: 28px;
    height: 28px;
    background: var(--paper);
    margin-bottom: 12px;
  }
  .wordmark__name { font-size: 30px; letter-spacing: 1.5px; line-height: 1; }
  .wordmark__sub { font-size: 10px; letter-spacing: 8px; margin-top: 6px; margin-right: -8px; }

  .card--details .wordmark { left: 318px; width: 192px; bottom: 60px; }
  .card--brand .wordmark { left: 50%; top: 50%; transform: translate(-50%, -50%); }
  .card--brand .wordmark__name { font-size: 34px; letter-spacing: 2px; }
  .card--brand .wordmark__sub { font-size: 11px; letter-spacing: 9px; margin-right: -9px; }
</style>
</head>
<body>

<section class="card card--details" aria-label="Business card, contact side">
  <div class="accent-band"></div>

  <div class="contact">
    <h1 class="contact__name">Paul Whitcombe</h1>
    <p class="contact__role">Managing Partner</p>
    <ul class="contact__list">
      <li><svg viewBox="0 0 10 10" aria-hidden="true"><path d="M2 0.5 L3.6 2.6 L2.7 3.6 Q3.8 5.8 6.2 7.2 L7.2 6.3 L9.5 7.8 L8.4 9.5 Q3.5 8.8 0.6 1.8 Z"/></svg>02 9364 2710</li>
      <li><svg viewBox="0 0 10 10" aria-hidden="true"><path d="M3 0 H7 Q8 0 8 1 V9 Q8 10 7 10 H3 Q2 10 2 9 V1 Q2 0 3 0 Z M3 1.2 V7.8 H7 V1.2 Z"/></svg>02 8472 3159</li>
      <li><svg viewBox="0 0 10 10" aria-hidden="true"><path d="M0.5 2 H9.5 V8 H0.5 Z M1.3 2.8 V7.2 H8.7 V2.8 L5 5.4 Z" fill-rule="evenodd"/></svg>paul@qvlegal.com.au</li>
    </ul>
    <p class="contact__address">Level 9, 7 Ferris Lane<br>Sydney NSW 2000<br>www.qvlegal.com.au</p>
  </div>

  <div class="wordmark">
    <span class="wordmark__square"></span>
    <span class="wordmark__name">QUAYVALE</span>
    <span class="wordmark__sub">LAWYERS</span>
  </div>
</section>

<section class="card card--brand" aria-label="Business card, brand side">
  <div class="wordmark">
    <span class="wordmark__square"></span>
    <span class="wordmark__name">QUAYVALE</span>
    <span class="wordmark__sub">LAWYERS</span>
  </div>
</section>

</body>
</html>
```